Association qui souhaite améliorer l'accès aux personnes en situation de handicap

Nous sommes une association qui a pour objectif d'améliorer l'accessibilité, augmenter l'offre des activités réalisables dans notre région touristique.
Nous souhaitons réaliser un site internet afin de pouvoir communiquer sur notre association. Nous avons déjà conçu notre flyer sur Plumotrix. Nous souhaiterions une base graphique se rapportant à celui-ci. C'est possible de tout retravailler mais nous souhaitons tout de même retrouver la charte graphique ou code couleur du flyer.
Il nous faudrait quelques pages:
- 1 page : Acceuil / Présentation (Home), Il y aurait le descriptif de l'association, avec ses objectifs à +/- moyen terme
- 1 page : Nos réalisations, celle-ci présenterait les éléments que nous avons réalisés avec des zones de textes et des images classées chronologiquement au fur et à mesure des nouveautés
- 1 page : Media, comme la précédente, mais ou on pourrait voir ou lire sur les divers médias qui parlent de nous
- 1 page : Evenements : c'est une page pour présenter divers activités que nous allons organiser
- 1 page : Contact qui indique comment nous contacter et avec la présentation des 5 ou 6 membres du comité
- 1 link donate : qui arrive sur un formulaire de donnée que l'on pourra faire évoluer sur un système de payement par la suite. Cette bannière doit se retrouver sur toutes les pages
Il est nécessaire que se design puisse être transféré sur une lecture sur téléphone mobile
Personnes en situation de handicap
Associatif

```html
<!DOCTYPE html>
<html lang="en">
<head>
<meta charset="utf-8">
<title>Openway Association</title>
<link href="https://fonts.googleapis.com/css2?family=Bebas+Neue&family=Raleway:wght@500;600;700&family=Mulish:wght@400;600;700&display=swap" rel="stylesheet">
<style>
:root{
  --red:#c1182b;
  --dark:#2a3036;
  --ink:#1d1d1f;
  --text:#444;
  --white:#fff;
  --cream:#fbfaf4;
  --line:#9a9a9a;
}
*{margin:0;padding:0;box-sizing:border-box}
html,body{width:1200px;height:3333px;overflow:hidden}
body{position:relative;background:var(--white);font-family:'Mulish',sans-serif;color:var(--text)}
.abs{position:absolute}
.btn{position:absolute;background:var(--red);color:var(--white);font:700 11px 'Mulish',sans-serif;text-transform:uppercase;border-radius:20px;width:118px;height:39px;display:flex;align-items:center;justify-content:center;letter-spacing:.3px}
.condensed{font-family:'Bebas Neue',sans-serif;letter-spacing:.5px}

/* top bar & nav */
.topbar{left:0;top:0;width:1200px;height:28px;background:var(--red)}
.social-dot{width:9px;height:9px;border-radius:50%;background:var(--white)}
.topbar .social-dot{left:130px;top:10px}
.topbar .mail{right:128px;top:7px;color:var(--white);font-size:11px;display:flex;align-items:center;gap:6px}
.nav{left:0;top:28px;width:1200px;height:62px;background:var(--white)}
.brand{display:flex;align-items:center;gap:8px;font:700 15px 'Raleway',sans-serif;color:var(--dark);line-height:1}
.brand-square{width:22px;height:22px;background:var(--red)}
.nav .brand{left:130px;top:20px}
.menu{left:539px;top:25px;display:flex;gap:41px;font-size:11px;color:var(--ink)}
.menu .active{color:var(--red);position:relative}
.nav .donate{left:977px;top:16px;height:30px;width:94px}

/* hero */
.hero{left:0;top:90px;width:1200px;height:443px;background:linear-gradient(180deg,#3d4a40 0%,#5f6e63 45%,#a9b3ad 75%,#7c8179 100%)}
.hero-photo{left:560px;top:0;width:640px;height:443px;background:radial-gradient(ellipse at 60% 55%,#c9cec9 0%,#8e978f 45%,transparent 75%)}
.hero .kicker{left:130px;top:120px;font-size:30px;color:var(--white)}
.hero h1{left:130px;top:153px;font:700 44px 'Raleway',sans-serif;color:var(--white)}
.hero h1 span{color:var(--red)}
.hero p{left:130px;top:218px;width:430px;font-size:13px;line-height:19px;color:var(--white)}
.hero .btn{left:130px;top:279px}
.dots{left:131px;top:408px;display:flex;gap:11px}
.dots i{width:11px;height:11px;border-radius:50%;background:var(--white)}
.dots i.on{background:var(--red)}

/* welcome */
.welcome-photo{left:130px;top:599px;width:400px;height:366px;border-radius:32px;background:linear-gradient(135deg,#4f6d2c,#c4c8b4 45%,#e7e2d5 55%,#3c5a24)}
.welcome .kicker{left:610px;top:638px;font-size:20px;color:var(--ink)}
.section-title{font:500 34px 'Raleway',sans-serif;color:var(--ink)}
.welcome h2{left:610px;top:665px}
.welcome h2 span{color:var(--red)}
.body-copy{font-size:13px;line-height:19.4px;color:var(--text)}
.welcome p{left:610px;top:726px;width:460px}
.welcome .btn{left:610px;top:870px}

/* achievements */
.achievements{left:0;top:1031px;width:1200px;height:515px;background:linear-gradient(90deg,#2e3538 0%,#3b4440 60%,#4a544c 100%)}
.achievements svg{left:0;top:0}
.achievements h2{left:132px;top:125px;color:var(--white)}
.achievements p{left:132px;top:192px;width:460px;color:var(--white)}
.achievements .btn{left:132px;top:342px}

/* media */
.media h2{left:0;top:1602px;width:1200px;text-align:center}
.media .sub{left:0;top:1652px;width:1200px;text-align:center;font-size:13px}
.media-card{top:1699px;width:300px;height:180px}
.media-card .label{position:absolute;left:27px;top:160px;width:247px;height:41px;background:var(--white);box-shadow:0 2px 8px rgba(0,0,0,.12);display:flex;align-items:center;justify-content:center;font-size:13px;color:var(--ink);gap:6px}
.media-card .label b{color:var(--red);font-size:16px}

/* events */
.events{left:0;top:1967px;width:1200px;height:568px;background:linear-gradient(180deg,#3a4047,#2e3238)}
.events h2{left:0;top:63px;width:1200px;text-align:center;color:var(--white)}
.event-card{top:128px;width:300px;height:370px;background:var(--white)}
.event-photo{left:0;top:0;width:300px;height:208px}
.date{left:12px;top:12px;width:38px;height:41px;background:var(--red);color:var(--white);font-size:9px;text-align:center;line-height:12px;padding-top:8px}
.event-card h3{left:22px;top:224px;font:600 16px 'Raleway',sans-serif;color:var(--ink)}
.event-card p{left:23px;top:257px;width:260px;font-size:12.5px;line-height:19px}
.event-card .btn{left:24px;top:331px}

/* contact */
.contact{left:0;top:2535px;width:1200px;height:420px;background:var(--cream)}
.contact-photo{left:130px;top:2602px;width:400px;height:317px;border-radius:32px;background:linear-gradient(135deg,#7d9a52,#a3a29a 40%,#b93342 62%,#5d6a4d)}
.contact h2{left:608px;top:2641px}
.contact .sub{left:610px;top:2689px;font-size:13px;color:var(--ink)}
.field{border:1px solid var(--line);background:var(--white);font-size:10px;color:#666;padding:10px 9px}
.submit{background:var(--red);color:var(--white);font-size:10px;display:flex;align-items:center;justify-content:center}

/* footer */
.footer{left:0;top:2870px;width:1200px;height:463px}
.footer .brand{left:130px;top:190px;color:var(--white)}
.footer .about{left:130px;top:245px;width:210px;font-size:10.5px;line-height:16px;color:var(--white)}
.footer .social-dot{left:130px;top:307px;width:21px;height:21px;background:var(--red)}
.col h4{font-family:'Bebas Neue',sans-serif;font-weight:400;font-size:19px;color:var(--red);letter-spacing:.5px;margin-bottom:6px}
.col li{list-style:none;font-size:10.5px;color:var(--white);line-height:22.6px}
.contact-line{display:flex;gap:9px;align-items:flex-start;font-size:10.5px;color:var(--white);line-height:13px;margin-bottom:12px}
.contact-line i{width:21px;height:21px;border:1.5px solid var(--white);border-radius:50%;display:flex;align-items:center;justify-content:center;flex:none}
.contact-line i::after{content:"";width:9px;height:9px;border-radius:50%;background:var(--red)}
.copyright{left:0;top:402px;width:1200px;text-align:center;font-size:10.5px;color:var(--white)}
.copyright span{color:var(--red)}
</style>
</head>
<body>

<header>
  <div class="abs topbar">
    <span class="abs social-dot" aria-hidden="true"></span>
    <div class="abs mail">
      <svg width="12" height="9" viewBox="0 0 12 9"><rect x=".5" y=".5" width="11" height="8" fill="none" stroke="#fff"/><path d="M.5 .5 6 5l5.5-4.5" fill="none" stroke="#fff"/></svg>
      info@openway-association.org
    </div>
  </div>
  <nav class="abs nav">
    <div class="abs brand"><span class="brand-square"></span>Openway Association</div>
    <div class="abs menu">
      <span class="active">Home
        <svg class="abs" style="left:0;top:17px" width="32" height="7" viewBox="0 0 32 7"><path d="M1 1l6 5 6-5 6 5 6-5 6 5" fill="none" stroke="#c1182b" stroke-width="1.6"/></svg>
      </span>
      <span>Our Achievements</span>
      <span>Media</span>
      <span>Events</span>
      <span>Contacts</span>
    </div>
    <span class="btn donate">Donate</span>
  </nav>
</header>

<section class="abs hero">
  <div class="abs hero-photo" role="img" aria-label="Woman in a wheelchair beside a misty forest lake"></div>
  <div class="abs kicker condensed">Access the</div>
  <h1 class="abs">TOURIST <span>REGION</span></h1>
  <p class="abs">The resources of the association come from subscriptions, donations and events organized throughout the year.</p>
  <span class="btn">Read more</span>
  <div class="abs dots"><i class="on"></i><i></i><i></i></div>
</section>

<section class="welcome">
  <div class="abs welcome-photo" role="img" aria-label="Man with a white cane walking between garden columns"></div>
  <div class="abs kicker condensed">Welcome to</div>
  <h2 class="abs section-title">Openway <span>Association</span></h2>
  <p class="abs body-copy">Sed ut perspiciatis unde omnis iste natus error sit voluptatem accusantium doloremque laudantium, totam rem aperiam, eaque ipsa quae ab illo inventore veritatis et quasi architecto beatae vitae dicta sunt explicabo. Nemo enim ipsam voluptatem quia voluptas sit aspernatur aut odit aut fugit, sed quia consequuntur magni dolores eos qui ratione voluptatem sequi nesciunt.</p>
  <span class="btn">Read more</span>
</section>

<section class="abs achievements">
  <svg class="abs" width="1200" height="515" viewBox="0 0 1200 515">
    <defs>
      <linearGradient id="field" x1="0" y1="0" x2="1" y2="1">
        <stop offset="0" stop-color="#6d7a5e"/>
        <stop offset=".45" stop-color="#8a9a58"/>
        <stop offset=".8" stop-color="#4b5a2d"/>
        <stop offset="1" stop-color="#7a2a33"/>
      </linearGradient>
    </defs>
    <polygon points="729,0 598,263 1069,515 1200,515 1200,0" fill="url(#field)" role="img" aria-label="Hand touching tall grass beside a wheelchair wheel"/>
    <polyline points="729,0 598,263 1069,515" fill="none" stroke="#fff" stroke-width="6"/>
  </svg>
  <h2 class="abs section-title">Our Achievements</h2>
  <p class="abs body-copy">Sed ut perspiciatis unde omnis iste natus error sit voluptatem accusantium doloremque laudantium, totam rem aperiam, eaque ipsa quae ab illo inventore veritatis et quasi architecto beatae vitae dicta sunt explicabo. Nemo enim ipsam voluptatem quia voluptas sit aspernatur aut odit aut fugit, sed quia consequuntur magni dolores eos qui ratione voluptatem sequi nesciunt.</p>
  <span class="btn">Read more</span>
</section>

<section class="media">
  <h2 class="abs section-title">Our Media</h2>
  <div class="abs sub">Sed ut perspiciatis unde omnis iste natus error sit voluptatem</div>
  <div class="abs media-card" style="left:130px">
    <div class="abs" style="inset:0;background:linear-gradient(135deg,#4d6e2e,#c9d0c6 55%,#7e9a52)" role="img" aria-label="Elderly woman in a wheelchair greeted by a visitor"></div>
    <div class="label">Voluptas Sit Aspernatur <b>+</b></div>
  </div>
  <div class="abs media-card" style="left:450px">
    <div class="abs" style="inset:0;background:linear-gradient(135deg,#dfe3e6,#8a8f94 50%,#eef0f2)" role="img" aria-label="People helping a woman in the snow"></div>
    <div class="label">Voluptas Sit Aspernatur <b>+</b></div>
  </div>
  <div class="abs media-card" style="left:770px">
    <div class="abs" style="inset:0;background:linear-gradient(135deg,#cfc8a8,#e8e6dc 50%,#6d7f96)" role="img" aria-label="Doctor examining a seated patient"></div>
    <div class="label">Voluptas Sit Aspernatur <b>+</b></div>
  </div>
</section>

<section class="abs events">
  <h2 class="abs section-title">Recent Event</h2>
  <article class="abs event-card" style="left:130px">
    <div class="abs event-photo" style="background:linear-gradient(135deg,#5e8e35,#4d3f9a 60%,#6fa13e)" role="img" aria-label="Girl blowing a dandelion on a lawn"></div>
    <div class="abs date">12<br>MAY</div>
    <h3 class="abs">Neque Porro Wuisquam</h3>
    <p class="abs">Sed ut perspiciatis unde omnis iste natus error sit voluptatem accusantium</p>
    <span class="btn">Read more</span>
  </article>
  <article class="abs event-card" style="left:450px">
    <div class="abs event-photo" style="background:linear-gradient(135deg,#3f4a3a,#9aa19a 50%,#5a5f5c)" role="img" aria-label="Group of wheelchair users gathered on a terrace"></div>
    <div class="abs date">12<br>MAY</div>
    <h3 class="abs">Neque Porro Wuisquam</h3>
    <p class="abs">Sed ut perspiciatis unde omnis iste natus error sit voluptatem accusantium</p>
    <span class="btn">Read more</span>
  </article>
  <article class="abs event-card" style="left:770px">
    <div class="abs event-photo" style="background:linear-gradient(135deg,#7f9b60,#2f4c8c 50%,#8a8c7a)" role="img" aria-label="Wheelchair basketball players on an outdoor court"></div>
    <div class="abs date">12<br>MAY</div>
    <h3 class="abs">Neque Porro Wuisquam</h3>
    <p class="abs">Sed ut perspiciatis unde omnis iste natus error sit voluptatem accusantium</p>
    <span class="btn">Read more</span>
  </article>
</section>

<section>
  <div class="abs contact"></div>
  <div class="abs contact-photo" role="img" aria-label="Man riding an adapted all-terrain vehicle in the hills"></div>
  <h2 class="abs section-title" style="left:608px;top:2641px">Contact Us</h2>
  <div class="abs sub" style="left:610px;top:2689px;font-size:13px;color:var(--ink)">Sed ut perspiciatis unde omnis iste natus error</div>
  <form>
    <div class="abs field" style="left:610px;top:2742px;width:227px;height:35px">Name:</div>
    <div class="abs field" style="left:610px;top:2789px;width:227px;height:35px">Email:</div>
    <div class="abs field" style="left:610px;top:2836px;width:227px;height:35px">Phone:</div>
    <div class="abs field" style="left:843px;top:2742px;width:227px;height:82px">Comments:</div>
    <div class="abs submit" style="left:843px;top:2836px;width:227px;height:35px">SUBMIT</div>
  </form>
</section>

<footer class="abs footer">
  <svg class="abs" style="left:0;top:0" width="1200" height="463" viewBox="0 0 1200 463">
    <polygon points="0,55 472,127 1200,3 1200,463 0,463" fill="#2a3036"/>
  </svg>
  <div class="abs brand"><span class="brand-square"></span>Openway Association</div>
  <p class="abs about">Sed ut perspiciatis unde omnis iste natus error sit voluptatem accusantium rem aperiam</p>
  <span class="abs social-dot" aria-hidden="true"></span>
  <div class="abs col" style="left:449px;top:170px">
    <h4>Sitemap</h4>
    <ul><li>Home</li><li>Our Achivements</li><li>Media</li><li>Events</li><li>Contact Us</li></ul>
  </div>
  <div class="abs col" style="left:669px;top:170px">
    <h4>Others</h4>
    <ul><li>Privacy Policy</li><li>Terms &amp; Conditions</li><li>Leagal</li><li>Donate</li><li>Help / Support</li></ul>
  </div>
  <div class="abs col" style="left:876px;top:170px">
    <h4>Contacts</h4>
    <div class="contact-line" style="margin-top:10px"><i></i><span>Rue des Tilleuls 12 / 1000<br>Valmont</span></div>
    <div class="contact-line"><i></i><span style="padding-top:4px">info@openway-association.org</span></div>
  </div>
  <div class="abs copyright">Copyright © 2022 <span>Openway Association</span>. All Rights Reserved.</div>
</footer>

</body>
</html>
```